Thornvale Agribusiness Consulting needs a Website Design.

We need a website design for a new company based in UK. Thornvale offers agribusiness consulting and farm design services to farmers, smallholders and the wider agribusiness industry to assist clients in adopting more sustainable and regenerative production, processing and marketing practices.
Services are offered face-to-face and on a remote platform.
Services are offered in the UK and overseas.
We would like to see designs that reflect the natural environment, business and sustainability. Desired colours; green, blue, grey. The final design should communicate professionalism in the rural economy.
The design should be able to be customized by the client to make future changes and additions.
Target Market(s)
Farmers, smallholders, and the agricultural industry in UK and overseas.
Industry/Entity Type
Agribusiness
Number of Pages Required
4 page
Look and feel
Each slider illustrates characteristics of the customer's brand and the style your logo design should communicate.

```html
<!DOCTYPE html>
<html lang="en">
<head>
<meta charset="utf-8">
<title>Thornvale Agribusiness Consulting</title>
<link href="https://fonts.googleapis.com/css2?family=Bitter:wght@400;700&family=Open+Sans:wght@400;600&display=swap" rel="stylesheet">
<style>
  :root {
    --green: #8cc63e;
    --teal: #16997c;
    --blue: #1479c0;
    --ink: #222222;
    --body: #444444;
    --footer: #383838;
    --footer-text: #bcbcbc;
    --line: #e2e2e2;
  }
  * { margin: 0; padding: 0; box-sizing: border-box; }
  html, body { width: 800px; height: 1200px; overflow: hidden; background: #fff; }
  body { position: relative; font-family: 'Open Sans', sans-serif; color: var(--body); }

  .site-header { position: absolute; left: 0; top: 0; width: 800px; height: 70px; border-top: 2px solid var(--green); background: #fff; }
  .brand { position: absolute; left: 66px; top: 25px; font-family: 'Bitter', serif; font-weight: 700; font-size: 21px; letter-spacing: 0.5px; color: var(--ink); }
  .main-nav a { position: absolute; top: 33px; font-family: 'Bitter', serif; font-size: 11px; color: var(--ink); text-decoration: none; letter-spacing: 0.3px; }
  .main-nav a.active { color: var(--green); }
  .nav-marker { position: absolute; left: 366px; top: 66px; width: 44px; height: 4px; background: var(--green); }

  .hero { position: absolute; left: 0; top: 70px; width: 800px; height: 300px; overflow: hidden; }
  .hero-photo { position: absolute; inset: 0; background: linear-gradient(180deg, #5d8a3a 0%, #7da74a 25%, #8bbd4a 55%, #6f9f38 100%); }
  .hero-panel { position: absolute; left: 66px; top: 0; width: 223px; height: 300px; background: rgba(140, 198, 62, 0.9); }
  .hero-kicker { position: absolute; left: 17px; top: 50px; font-family: 'Bitter', serif; font-size: 18px; color: #fff; }
  .hero-title { position: absolute; left: 12px; top: 70px; font-family: 'Bitter', serif; font-size: 38px; color: #fff; }
  .hero-text { position: absolute; left: 13px; top: 124px; width: 205px; font-size: 8.6px; line-height: 13.5px; color: #fff; }
  .hero-btn { position: absolute; left: 14px; top: 170px; width: 86px; height: 33px; background: #222; color: #fff; font-family: 'Bitter', serif; font-size: 10.5px; line-height: 33px; text-align: center; border-radius: 2px; }
  .dots span { position: absolute; top: 219px; width: 7px; height: 7px; border-radius: 50%; background: #d9eec0; }
  .dots span.on { background: #222; }
  .hero-curve { position: absolute; left: 0; top: 0; }

  .section-title { font-family: 'Bitter', serif; font-weight: 400; font-size: 21px; color: var(--ink); letter-spacing: 0.3px; }
  .industry-title { position: absolute; left: 0; top: 331px; width: 808px; text-align: center; }

  .industry-card { position: absolute; top: 414px; width: 214px; height: 172px; color: #fff; text-align: center; box-shadow: 0 6px 6px -5px rgba(0,0,0,0.25); }
  .industry-card h3 { position: absolute; left: 0; right: 0; top: 66px; font-family: 'Bitter', serif; font-weight: 400; font-size: 21px; letter-spacing: 0.5px; }
  .industry-card p { position: absolute; left: 14px; right: 14px; top: 103px; font-size: 8.6px; line-height: 13.8px; }
  .card-farmers { left: 66px; background: var(--green); }
  .card-smallholders { left: 293px; background: var(--teal); }
  .card-agri { left: 520px; background: var(--blue); }
  .card-badge { position: absolute; top: 362px; width: 100px; height: 100px; }

  .services { position: absolute; left: 0; top: 625px; width: 800px; height: 250px; border-top: 1px solid var(--line); border-bottom: 1px solid var(--line); background: linear-gradient(180deg, #ffffff 0%, #f1f1f1 60%, #ebebeb 100%); }
  .services-title { position: absolute; left: 65px; top: 32px; }
  .service-tile { position: absolute; top: 75px; width: 164px; height: 134px; }
  .service-photo { position: absolute; left: 0; top: 0; width: 164px; height: 96px; }
  .service-label { position: absolute; left: 0; top: 96px; width: 164px; height: 38px; padding-left: 12px; font-family: 'Bitter', serif; font-size: 14.5px; line-height: 40px; color: #fff; letter-spacing: 0.5px; text-shadow: 0 1px 2px rgba(0,0,0,0.35); }

  .welcome-title { position: absolute; left: 64px; top: 910px; }
  .welcome-text { position: absolute; left: 66px; width: 360px; font-size: 8.6px; line-height: 13.6px; color: #333; }
  .btn-green { position: absolute; left: 66px; top: 1053px; width: 77px; height: 38px; background: var(--green); color: #fff; font-family: 'Bitter', serif; font-size: 11px; line-height: 38px; text-align: center; border-radius: 2px; }

  .news { position: absolute; left: 441px; top: 916px; width: 295px; height: 174px; border: 1px solid #dcdcdc; background: linear-gradient(180deg, #ffffff 0%, #f0f0f0 100%); }
  .news-title { position: absolute; left: 22px; top: 20px; }
  .news-arrows { position: absolute; left: 252px; top: 27px; }
  .news-photo { position: absolute; left: 24px; top: 67px; width: 111px; height: 87px; background: linear-gradient(180deg, #caa56f 0%, #b88c52 60%, #a47a44 100%); }
  .news-head { position: absolute; left: 146px; top: 67px; font-weight: 600; font-size: 10px; color: var(--green); letter-spacing: 0.2px; }
  .news-date { position: absolute; left: 147px; top: 86px; font-size: 7.6px; color: #333; }
  .news-text { position: absolute; left: 146px; top: 104px; width: 130px; font-size: 7.8px; line-height: 10.4px; color: #333; }
  .news-more { position: absolute; left: 147px; top: 141px; font-size: 7.8px; color: var(--green); }

  .site-footer { position: absolute; left: 0; top: 1133px; width: 800px; height: 67px; background: var(--footer); }
  .footer-nav a { position: absolute; top: 22px; font-family: 'Bitter', serif; font-size: 7.6px; color: var(--footer-text); text-decoration: none; letter-spacing: 0.3px; }
  .copyright { position: absolute; left: 67px; top: 39px; font-family: 'Bitter', serif; font-size: 7.2px; color: var(--footer-text); }
  .social span { position: absolute; top: 26px; width: 12px; height: 12px; border-radius: 2px; }
</style>
</head>
<body>

<header class="site-header">
  <div class="brand">THORNVALE</div>
  <nav class="main-nav">
    <a class="active" href="#" style="left:373px">HOME</a>
    <a href="#" style="left:435px">ABOUT US</a>
    <a href="#" style="left:518px">SERVICES</a>
    <a href="#" style="left:598px">CLIENTS</a>
    <a href="#" style="left:671px">CONTACT US</a>
  </nav>
  <div class="nav-marker"></div>
</header>

<section class="hero">
  <div class="hero-photo" role="img" aria-label="Herd of dairy cows grazing in a green pasture with trees behind"></div>
  <div class="hero-panel">
    <div class="hero-kicker">Agri Business</div>
    <div class="hero-title">Consulting</div>
    <p class="hero-text">Neque porro quisquam est, qui dolorem ipsum quia dolor sit amet, consectetur.</p>
    <div class="hero-btn">READ MORE</div>
    <div class="dots">
      <span class="on" style="left:18px"></span>
      <span style="left:32px"></span>
      <span style="left:45px"></span>
    </div>
  </div>
  <svg class="hero-curve" width="800" height="300" viewBox="0 0 800 300">
    <path d="M0 296 Q400 180 800 296 L800 300 L0 300 Z" fill="#fff"/>
  </svg>
</section>

<h2 class="section-title industry-title">OUR INDUSTRY</h2>

<article class="industry-card card-farmers">
  <h3>FARMERS</h3>
  <p>Neque porro quisquam est, qui dolorem ipsum quia dolor sit amet, consectetur, adipisci velit, sed quia non numquam eius</p>
</article>
<article class="industry-card card-smallholders">
  <h3>SMALLHOLDERS</h3>
  <p>Neque porro quisquam est, qui dolorem ipsum quia dolor sit amet, consectetur, adipisci velit, sed quia non numquam eius</p>
</article>
<article class="industry-card card-agri">
  <h3>AGRI BUSINESS</h3>
  <p>Neque porro quisquam est, qui dolorem ipsum quia dolor sit amet, consectetur, adipisci velit, sed quia non numquam eius</p>
</article>

<svg class="card-badge" style="left:123px" viewBox="0 0 100 100" aria-label="Home icon">
  <circle cx="50" cy="50" r="50" fill="#fff"/>
  <circle cx="50" cy="50" r="41" fill="#8cc63e"/>
  <path d="M32 50 L50 34 L68 50 M37 46 V66 H63 V46" fill="none" stroke="#fff" stroke-width="4" stroke-linejoin="round"/>
  <rect x="46" y="54" width="8" height="12" fill="#fff"/>
</svg>
<svg class="card-badge" style="left:350px" viewBox="0 0 100 100" aria-label="Location pin icon">
  <circle cx="50" cy="50" r="50" fill="#fff"/>
  <circle cx="50" cy="50" r="41" fill="#16997c"/>
  <path d="M50 70 C42 58 37 51 37 44 A13 13 0 0 1 63 44 C63 51 58 58 50 70 Z" fill="#fff"/>
  <circle cx="50" cy="44" r="5" fill="#16997c"/>
</svg>
<svg class="card-badge" style="left:578px" viewBox="0 0 100 100" aria-label="Bar chart icon">
  <circle cx="50" cy="50" r="50" fill="#fff"/>
  <circle cx="50" cy="50" r="41" fill="#1479c0"/>
  <g fill="#fff">
    <rect x="35" y="52" width="7" height="15"/>
    <rect x="46.5" y="43" width="7" height="24"/>
    <rect x="58" y="34" width="7" height="33"/>
  </g>
</svg>

<section class="services">
  <h2 class="section-title services-title">OUR SERVICES</h2>
  <div class="service-tile" style="left:66px">
    <div class="service-photo" role="img" aria-label="Open field under a blue sky, half grass and half ploughed soil" style="background:linear-gradient(180deg,#3f7fd0 0%,#a9cdea 45%,#6c9a3a 60%,#b9ad97 100%)"></div>
    <div class="service-label" style="background:var(--green)">SUSTAINABLE</div>
  </div>
  <div class="service-tile" style="left:234px">
    <div class="service-photo" role="img" aria-label="Wooden farm gate before green rolling fields" style="background:linear-gradient(180deg,#9fb0bf 0%,#c6cfd4 30%,#4f6b34 45%,#7b8f4a 70%,#8f7a5a 100%)"></div>
    <div class="service-label" style="background:var(--teal)">REGENERATIVE</div>
  </div>
  <div class="service-tile" style="left:402px">
    <div class="service-photo" role="img" aria-label="Tray of white and brown eggs" style="background:linear-gradient(135deg,#e8e6e3 0%,#cfcac4 50%,#e4dfda 100%)"></div>
    <div class="service-label" style="background:var(--blue)">PROCESSING</div>
  </div>
  <div class="service-tile" style="left:570px">
    <div class="service-photo" role="img" aria-label="Crates of fresh local vegetables at a market stall" style="background:linear-gradient(135deg,#4f7a2e 0%,#a4503a 45%,#6f8f3a 70%,#3b3b36 100%)"></div>
    <div class="service-label" style="background:var(--green)">MARKETING</div>
  </div>
</section>

<h2 class="section-title welcome-title">WELCOME TO THORNVALE</h2>
<p class="welcome-text" style="top:951px">Nemo enim ipsam voluptatem quia voluptas sit aspernatur aut odit aut fugit, sed quia consequuntur magni dolores eos qui ratione voluptatem sequi nesciunt.</p>
<p class="welcome-text" style="top:992px">Neque porro quisquam est, qui dolorem ipsum quia dolor sit amet, consectetur, adipisci velit, sed quia non numquam eius modi tempora incidunt ut labore et dolore magnam aliquam quaerat voluptatem.</p>
<div class="btn-green">Read More</div>

<aside class="news">
  <h2 class="section-title news-title">LATEST NEWS</h2>
  <svg class="news-arrows" width="22" height="14" viewBox="0 0 22 14">
    <path d="M7 2 L2 7 L7 12 M15 2 L20 7 L15 12" fill="none" stroke="#222" stroke-width="1.6"/>
  </svg>
  <div class="news-photo" role="img" aria-label="Harvested field with round hay bales"></div>
  <div class="news-head">LOREM IPSUM DOLOR</div>
  <div class="news-date">MAY 02,2015</div>
  <p class="news-text">Neque porro quisquam est, qui dolorem ipsum quia dolor sit amet, consectetur...</p>
  <div class="news-more">Read More</div>
</aside>

<footer class="site-footer">
  <nav class="footer-nav">
    <a href="#" style="left:66px">HOME</a>
    <a href="#" style="left:114px">ABOUT US</a>
    <a href="#" style="left:179px">SERVICES</a>
    <a href="#" style="left:241px">CLIENTS</a>
    <a href="#" style="left:298px">CONTACT US</a>
  </nav>
  <div class="copyright">© 2015 THORNVALE. ALL RIGHTS RESERVED.</div>
  <div class="social">
    <span style="left:682px;background:#3b5a9a"></span>
    <span style="left:701px;background:#29a9e1"></span>
    <span style="left:721px;background:#f07a1e"></span>
  </div>
</footer>

</body>
</html>
```